Lotus Ridge Website

We need a website that has clean, asian looking images that relax and motivate people to come into our integrated medical center. My current website is www.needlecalmharbor.com and I would like the design for Lotus Ridge Wellness Partners to be similar but more inviting with video content and a product purchase store as well. A moving banner would be nice too. When people are looking for ways of losing weight or getting out of pain we want them to make the connection that we have the solution. This website needs to provide sufficient information so that patients are well informed and choose us as their health provider before they ever walk through our doors. We offer comprehensive natural medicine that is based on the principles that the body can heal itself when given the right conditions. Our services include medical weight loss and hormone balancing, acupuncture and chinese herbal medicine, physical medicine, trigger point injections, allergy testing and joint rehabilitation. The Medical Doctor and Licensed Acupuncturist work as a team to provide optimal care that is catered to each individual who comes through our doors.
Updates

Target Market(s)

40 to 50 year olds who want to lose weight or have pain issues.

Industry/Entity Type

Medical

Requirements
Must have
• Use photos from our website www.needlecalmharbor.com or similar content. Video content. Moving banner with relaxing images.
Nice to have
• Happy, healthy looking people. Medical Doctors working as a team. Friendly staff in a cutting edge facility.
Should not have
• Papyrus font, or big bold words.

```html
<!DOCTYPE html>
<html lang="en">
<head>
<meta charset="utf-8">
<title>Lotus Ridge Acupuncture</title>
<link href="https://fonts.googleapis.com/css2?family=Yanone+Kaffeesatz:wght@300;400&family=PT+Sans:wght@400;700&display=swap" rel="stylesheet">
<style>
  :root {
    --olive-top: #5b5b24;
    --olive-mid: #3f3e14;
    --olive-deep: #28270a;
    --nav-band: #262508;
    --accent: #8d8a2b;
    --accent-dark: #6f6c1e;
    --nav-text: #ebe8d2;
    --panel: #ffffff;
    --ink: #1f1f12;
    --body-ink: #3a3a30;
    --footer-ink: #7b7a4c;
    --frame: #4f4a1c;
    --share-a: #3f5f9f;
    --share-b: #8fd3e6;
  }
  * { margin: 0; padding: 0; box-sizing: border-box; }
  html, body { width: 1200px; height: 835px; overflow: hidden; }
  body {
    position: relative;
    font-family: "PT Sans", Tahoma, sans-serif;
    background: linear-gradient(180deg, var(--olive-top) 0%, #4e4d1b 36%, var(--olive-mid) 60%, var(--olive-deep) 100%);
  }
  .brand {
    position: absolute; left: 252px; top: 80px; width: 102px; height: 132px;
    background: #4c4b1a; border-radius: 6px;
    box-shadow: 0 14px 16px -10px rgba(0,0,0,.45);
    display: flex; flex-direction: column; align-items: center; justify-content: center; gap: 10px;
  }
  .brand-mark { width: 14px; height: 14px; border: 1.5px solid #f2f0e0; border-radius: 50%; }
  .brand-name {
    color: #f2f0e0; font-size: 12px; text-align: center; line-height: 1.3; letter-spacing: 1px;
  }
  .hero {
    position: absolute; left: 413px; top: 29px; width: 597px; height: 256px;
    border-radius: 3px; overflow: hidden;
    background: linear-gradient(90deg, #cfcfcf 0%, #e9e9e9 35%, #f4f1ee 55%, #e8d4c2 75%, #f6f2ee 100%);
  }
  .hero-photo { position: absolute; inset: 0; }
  .hero-title {
    position: absolute; left: 22px; top: 143px;
    font-family: "Yanone Kaffeesatz", sans-serif; font-weight: 300; font-size: 22px; color: #2a2a22;
  }
  .hero-caption {
    position: absolute; left: 0; top: 191px; width: 100%; height: 65px;
    background: linear-gradient(90deg, rgba(150,150,150,.55) 0%, rgba(150,150,150,.4) 55%, rgba(150,150,150,0) 80%);
    padding: 10px 22px; font-size: 12.5px; line-height: 27px; color: #2b2b22;
  }
  .main-nav {
    position: absolute; left: 0; top: 312px; width: 1200px; height: 50px;
    background: linear-gradient(180deg, #1f1e06, var(--nav-band));
  }
  .main-nav ul { list-style: none; position: absolute; left: 180px; top: 0; height: 50px; display: flex; }
  .main-nav li {
    position: relative; height: 50px; padding: 15px 17px 0 18px;
    font-family: "Yanone Kaffeesatz", sans-serif; font-weight: 300; font-size: 23px; color: var(--nav-text);
  }
  .main-nav li + li::before {
    content: ""; position: absolute; left: 0; top: 14px; width: 1px; height: 30px; background: #3d3c17;
  }
  .main-nav li.is-active { margin: 11px 12px 0; padding: 4px 13px 0; height: 39px; background: var(--accent); border-radius: 3px 3px 0 0; }
  .main-nav li.is-active + li::before { display: none; }
  .content {
    position: absolute; left: 180px; top: 362px; width: 835px; height: 413px;
    background: var(--panel); border-radius: 0 0 4px 4px;
  }
  .sub-nav {
    position: absolute; left: 4px; top: 0; width: 826px; height: 39px;
    background: var(--accent); border-radius: 0 0 4px 4px;
    list-style: none; display: flex; align-items: center;
  }
  .sub-nav li { position: relative; padding: 0 10px; font-size: 11px; color: #fff; white-space: nowrap; }
  .sub-nav li + li::before {
    content: ""; position: absolute; left: 0; top: -10px; width: 1px; height: 34px; background: var(--accent-dark);
  }
  .sub-nav li:first-child { padding-left: 10px; }
  .welcome { position: absolute; left: 32px; top: 62px; width: 520px; }
  .welcome h1 { font-weight: 400; font-size: 20px; color: var(--ink); }
  .welcome p { margin-top: 10px; font-size: 12.5px; line-height: 29.3px; color: var(--body-ink); }
  .spread { position: absolute; left: 32px; top: 300px; }
  .spread h2 { font-weight: 400; font-size: 15px; color: var(--ink); }
  .share-row { display: flex; gap: 20px; margin-top: 14px; }
  .share-btn {
    width: 102px; height: 36px; border-radius: 3px;
    display: flex; align-items: center; justify-content: center; gap: 8px;
    font-size: 13px; letter-spacing: .5px; color: #fff;
  }
  .share-btn .dot { width: 10px; height: 10px; background: #fff; opacity: .85; }
  .share-btn--one { background: linear-gradient(180deg, #5a7bbd, var(--share-a)); }
  .share-btn--two { background: linear-gradient(180deg, #b9e8f4, var(--share-b)); }
  .side { position: absolute; left: 625px; top: 64px; }
  .side h3 { font-weight: 400; font-size: 16px; color: var(--ink); }
  .video-thumb {
    position: relative; margin: 14px 0 0 3px; width: 176px; height: 124px;
    border: 2px solid var(--frame); border-radius: 3px;
    background: linear-gradient(135deg, #d9c1ad, #f1e4da 50%, #c9ad96);
  }
  .play {
    position: absolute; left: 66px; top: 37px; width: 40px; height: 40px; border-radius: 4px;
    background: rgba(90,80,70,.75);
  }
  .play svg { display: block; }
  .side h3.store-title { margin-top: 18px; margin-left: 4px; }
  .store-thumb {
    margin: 12px 0 0 1px; width: 180px; height: 129px;
    border: 2px solid var(--frame); border-radius: 3px;
    background: radial-gradient(circle at 60% 40%, #7d6a8e, #5a4968 70%);
  }
  .footer {
    position: absolute; left: 203px; top: 788px; font-size: 9px; color: var(--footer-ink);
  }
</style>
</head>
<body>
  <header>
    <div class="brand">
      <span class="brand-mark"></span>
      <span class="brand-name">LOTUS RIDGE<br>ACUPUNCTURE</span>
    </div>
    <section class="hero">
      <div class="hero-photo" role="img" aria-label="Photo of a relaxed woman lying down receiving acupuncture on her back"></div>
      <div class="hero-title">lorem ipsum dolor</div>
      <div class="hero-caption">Lorem ipsum dolor sit amet, consectetuer adipiscing elit,<br>sed diam nonummy nibh euismod tincidunt.</div>
    </section>
  </header>

  <nav class="main-nav">
    <ul>
      <li>home</li>
      <li>about us</li>
      <li class="is-active">service</li>
      <li>acupuncture</li>
      <li>biography</li>
      <li>nutrition</li>
      <li>my journey</li>
      <li>contact</li>
    </ul>
  </nav>

  <main class="content">
    <ul class="sub-nav">
      <li>weight loss</li>
      <li>hormone balancing</li>
      <li>acupuncture</li>
      <li>chinese herbal medicine</li>
      <li>physical medicine</li>
      <li>trigger point injections</li>
      <li>allergy testing</li>
      <li>joint rehabilitation</li>
    </ul>

    <article class="welcome">
      <h1>Welcome to our Lotus Ridge Acupunture</h1>
      <p>Lorem ipsum dolor sit amet, consectetuer adipiscing elit, sed diam nonummy nibh euismod tincidunt ut laoreet dolore magna aliquam erat volutpat. Ut wisi enim ad minim veniam, quis nostrud exerci tation ullamcorper suscipit lobortis nisl ut aliquip ex ea commodo consequat. Duis autem vel eum iriure dolor in hendrerit in vulputate velit esse molestie consequat, vel illum dolore eu feugiat nulla facilisis at vero eros et accumsan et iusto odio dignissim qui blandit praesent luptatum zzril delenit augue duis dolore te feugait nulla facilisi.</p>
    </article>

    <section class="spread">
      <h2>Spread the word about Lotus Ridge Acupuncture</h2>
      <div class="share-row">
        <span class="share-btn share-btn--one"><span class="dot"></span>SHARE</span>
        <span class="share-btn share-btn--two"><span class="dot"></span>SHARE</span>
      </div>
    </section>

    <aside class="side">
      <h3>Watch the Video</h3>
      <div class="video-thumb" role="img" aria-label="Video still of a facial acupuncture treatment">
        <span class="play"><svg width="40" height="40" viewBox="0 0 40 40"><path d="M15 11 L29 20 L15 29 Z" fill="#d8d2c8"/></svg></span>
      </div>
      <h3 class="store-title">Online Store</h3>
      <div class="store-thumb" role="img" aria-label="Product photo of a singing bowl and tuning forks"></div>
    </aside>
  </main>

  <footer class="footer">Copyright 2007© Lotus Ridge Acupuncture — All Rights Reserved</footer>
</body>
</html>
```